Modern Business Card

Modern professional business card with more than just logo and demographic info. Something memorable.

We are a trendy/modern chiropractic group with an emphasis on neurology, hence the minimalist-type brain logo. We want to convey that modern and technical aspect with professionalism and the elite nature of our practice environment.

```html
<!DOCTYPE html>
<html lang="en">
<head>
<meta charset="utf-8">
<title>Vertex Chiropractic – Business Card</title>
<link href="https://fonts.googleapis.com/css2?family=Cinzel:wght@500&family=Montserrat:wght@400;500&display=swap" rel="stylesheet">
<style>
  :root {
    --brand-blue: #4a80c1;
    --motif-tint: #e6eef8;
    --ink: #3a3d42;
    --paper: #ffffff;
    --backdrop: #d9d9d9;
    --rule: #3f72b5;
  }
  * { box-sizing: border-box; margin: 0; padding: 0; }
  html, body {
    width: 1200px; height: 930px; overflow: hidden;
    background: var(--backdrop);
  }
  .stage { position: relative; width: 1200px; height: 930px; }
  .card {
    position: absolute; top: 305px;
    width: 560px; height: 320px;
    border-radius: 18px; overflow: hidden;
    box-shadow: 0 6px 16px rgba(0,0,0,0.18);
  }

  /* Front */
  .card--front { left: 27px; background: var(--brand-blue); }
  .front-brand {
    position: absolute; left: 0; right: 0; top: 118px;
    display: flex; align-items: center; justify-content: center; gap: 18px;
    color: var(--paper);
  }
  .brand-dot { width: 64px; height: 64px; border-radius: 50%; background: var(--paper); }
  .brand-words { font-family: "Cinzel", serif; font-weight: 500; line-height: 1; }
  .brand-name { font-size: 54px; letter-spacing: 2px; }
  .brand-sub { font-size: 25px; letter-spacing: 1px; margin-top: 4px; }

  /* Back */
  .card--back { left: 613px; background: var(--paper); }
  .motif-field {
    position: absolute; left: 300px; top: 96px;
    width: 260px; height: 210px;
    border-radius: 40px 0 0 40px;
    background: linear-gradient(160deg, var(--motif-tint) 0%, #eef3fa 60%, rgba(238,243,250,0) 100%);
  }
  .name-band {
    position: absolute; left: 0; top: 78px;
    width: 420px; height: 84px;
    background: var(--brand-blue);
    color: var(--paper);
    padding: 36px 0 0 40px;
  }
  .person-name {
    font-family: "Cinzel", serif; font-weight: 500;
    font-size: 19px; letter-spacing: 1px; line-height: 1;
  }
  .person-role {
    font-family: "Montserrat", sans-serif; font-size: 12px;
    margin: 4px 0 0 12px;
  }
  .back-brand {
    position: absolute; left: 428px; top: 58px;
    display: flex; align-items: center; gap: 8px;
    color: var(--brand-blue);
    font-family: "Cinzel", serif; font-weight: 500; font-size: 17px; letter-spacing: 1px;
  }
  .back-brand .mark { width: 26px; height: 26px; border-radius: 50%; background: var(--brand-blue); }
  .divider {
    position: absolute; left: 40px; right: 40px; top: 214px;
    height: 1.5px; background: var(--rule);
  }
  .contact-list {
    position: absolute; left: 40px; top: 228px;
    list-style: none;
    font-family: "Montserrat", sans-serif; font-size: 14px; color: var(--ink);
  }
  .contact-list li { display: flex; align-items: center; gap: 10px; height: 21px; }
  .contact-list svg { width: 12px; height: 12px; flex: none; }
  .contact-list .accent { color: var(--brand-blue); }
  .address {
    position: absolute; right: 40px; top: 232px; text-align: right;
    font-family: "Montserrat", sans-serif; font-size: 14px; font-style: normal;
    color: var(--ink); line-height: 21px;
  }
  .foot-band {
    position: absolute; left: 0; right: 0; bottom: 0; height: 14px;
    background: var(--brand-blue);
  }
</style>
</head>
<body>
<main class="stage">
  <section class="card card--front" aria-label="Card front">
    <div class="front-brand">
      <span class="brand-dot"></span>
      <div class="brand-words">
        <div class="brand-name">VERTEX</div>
        <div class="brand-sub">CHIROPRACTIC</div>
      </div>
    </div>
  </section>

  <section class="card card--back" aria-label="Card back">
    <div class="motif-field" role="img" aria-label="Faint enlarged brand pattern in pale blue"></div>
    <div class="name-band">
      <p class="person-name">DANIEL BROOKS</p>
      <p class="person-role">Director</p>
    </div>
    <div class="back-brand"><span class="mark"></span>VERTEX</div>
    <div class="divider"></div>
    <ul class="contact-list">
      <li>
        <svg viewBox="0 0 24 24" fill="var(--brand-blue)"><path d="M6.6 10.8a15 15 0 0 0 6.6 6.6l2.2-2.2a1 1 0 0 1 1-.25 11.4 11.4 0 0 0 3.6.6 1 1 0 0 1 1 1V20a1 1 0 0 1-1 1A17 17 0 0 1 3 4a1 1 0 0 1 1-1h3.5a1 1 0 0 1 1 1c0 1.250.2 2.45.6 3.6a1 1 0 0 1-.25 1z"/></svg>
        (555) 214-6630
      </li>
      <li>
        <svg viewBox="0 0 24 24" fill="none" stroke="var(--brand-blue)" stroke-width="2.4"><rect x="3" y="5" width="18" height="14" rx="1"/><path d="M3 6l9 7 9-7"/></svg>
        info@vertexchiro.com
      </li>
      <li>
        <svg viewBox="0 0 24 24" fill="none" stroke="var(--brand-blue)" stroke-width="2"><circle cx="12" cy="12" r="9"/><path d="M3 12h18M12 3c3 3 3 15 0 18M12 3c-3 3-3 15 0 18"/></svg>
        <span>www.<span class="accent">vertexchiro</span>.com</span>
      </li>
    </ul>
    <address class="address">1187 Larkspur Lane<br>Salem, OR 97301</address>
    <div class="foot-band"></div>
  </section>
</main>
</body>
</html>
```